RB Halden Electric Yard Sign

Looking to have a yard sign designed that we can place at projects we are working on. Most likely will be 18" H x 24" W but flexible that we can increase the size if necessary. It should include our logo, our phone # 609-555-0147, website rbhaldenelectric.example and slogan, built on integrity, driven by excellence. Colors should match our brand.

```html
<!DOCTYPE html>
<html lang="en">
<head>
<meta charset="utf-8">
<title>RB Halden Electric Yard Sign</title>
<link rel="stylesheet" href="https://fonts.googleapis.com/css2?family=Montserrat:wght@600;700;800&display=swap">
<style>
  :root {
    --navy: #04356b;
    --red: #e31e27;
    --white: #ffffff;
    --backdrop: #eceef1;
  }
  * { margin: 0; padding: 0; box-sizing: border-box; }
  html, body {
    width: 1200px;
    height: 1200px;
    overflow: hidden;
    background: var(--backdrop);
  }
  .yard-sign {
    position: absolute;
    left: 40px;
    top: 180px;
    width: 1120px;
    height: 840px;
    background: var(--navy);
    overflow: hidden;
    font-family: "Montserrat", sans-serif;
    box-shadow: 0 6px 24px rgba(0, 0, 0, 0.12);
  }
  .footer-band {
    position: absolute;
    left: 0;
    top: 609px;
    width: 100%;
    height: 231px;
    background: var(--white);
  }
  .brand-panel {
    position: absolute;
    left: 83px;
    top: 0;
    width: 954px;
    height: 295px;
    background: var(--white);
    border-radius: 0 0 113px 113px;
    display: flex;
    align-items: center;
    justify-content: center;
    gap: 22px;
  }
  .brand-dot {
    width: 44px;
    height: 44px;
    border-radius: 50%;
    background: var(--navy);
  }
  .brand-name {
    color: var(--red);
    font-weight: 800;
    font-size: 66px;
    letter-spacing: 0.5px;
  }
  .slogan {
    position: absolute;
    left: 0;
    top: 318px;
    width: 100%;
    text-align: center;
    color: var(--white);
    font-weight: 800;
    font-size: 86px;
    line-height: 102px;
    letter-spacing: -0.5px;
  }
  .web-pill {
    position: absolute;
    left: 83px;
    top: 557px;
    width: 954px;
    height: 103px;
    background: var(--red);
    border-radius: 58px 0 58px 0;
    display: flex;
    align-items: center;
    justify-content: center;
    color: var(--white);
    font-weight: 700;
    font-size: 58px;
    letter-spacing: -0.3px;
  }
  .phone {
    position: absolute;
    left: 0;
    top: 672px;
    width: 100%;
    text-align: center;
    color: var(--navy);
    font-weight: 800;
    font-size: 128px;
    line-height: 140px;
    letter-spacing: -1px;
  }
</style>
</head>
<body>
  <div class="yard-sign">
    <div class="footer-band"></div>
    <div class="brand-panel">
      <span class="brand-dot"></span>
      <span class="brand-name">RB Halden Electric</span>
    </div>
    <p class="slogan">Built on Integrity,<br>Driven by Excellence</p>
    <div class="web-pill">rbhaldenelectric.example</div>
    <p class="phone">609-555-0147</p>
  </div>
</body>
</html>
```